Business Cards Design for the electrical wholesaler: clean bold dynamic :)

We need a business card design that would follow our latest brand guidelines. As an electrical wholesaler we want to bring a fresh look and feel into the industry. The design should be clean bold and dynamic. It should come alive with the renewed energy of our green colour. Our grey colour should keep things balanced and complement the notion of maturity and responsibility. We employ Lato as a corporate font however are not bound by this font and we’re open to interpretation here.

Target Market(s)

Electrical contractors

Industry/Entity Type

Business

Contact Information for Business Card

Logo
Name & Surname: Halyna Dorosh
Job Title: Director of Marketing
Email: halya.dorosh@quillmail.example
Cell phone: +1 780-555-0239
Address: 20517 - 87 Ave. Edmonton, AB, Canada. T6K 4N8
Business Phone: 780.555.0184
Website: www.brovix.example

Font styles to use
Other font styles liked:
• Lato

Requirements
Must have
• Logo & website
Nice to have
• Brand elements - some of them you may find in the attached Brand Guidelines (e.g. three lines on the background signifying "W")

```html
<!DOCTYPE html>
<html lang="en">
<head>
<meta charset="utf-8">
<title>Brovix Business Card</title>
<link href="https://fonts.googleapis.com/css2?family=Exo+2:wght@500;600&family=Lato:wght@400;700&display=swap" rel="stylesheet">
<style>
  :root {
    --backdrop: #3b3b3d;
    --card: #262627;
    --card-edge: #1c1c1d;
    --green: #8cc63f;
    --grey: #a7a7a9;
    --gloss: #4a4a4c;
    --white: #f2f2f2;
  }
  * { margin: 0; padding: 0; box-sizing: border-box; }
  html, body {
    width: 799px; height: 1200px; overflow: hidden;
    background: var(--backdrop);
  }
  body {
    display: flex; flex-direction: column; align-items: center; justify-content: center;
    gap: 110px;
    font-family: "Lato", sans-serif;
  }
  .card {
    position: relative;
    width: 640px; height: 366px;
    background: var(--card);
    border-radius: 22px;
    box-shadow: 0 1px 0 var(--card-edge), 0 18px 40px rgba(0,0,0,.35);
    overflow: hidden;
  }
  .card-front .wordmark {
    position: absolute; left: 50%; top: 50%;
    transform: translate(-50%, -50%);
    display: flex; align-items: center; gap: 22px;
  }
  .wordmark-dot {
    width: 58px; height: 58px; border-radius: 8px;
    background: var(--gloss);
  }
  .card-front .wordmark-name {
    font-family: "Lato", sans-serif; font-weight: 400;
    font-size: 104px; line-height: 1; letter-spacing: -1px;
    color: var(--gloss);
  }
  .accent-arc { position: absolute; left: 0; top: 0; }
  .identity { position: absolute; left: 44px; top: 30px; }
  .identity-name {
    font-family: "Exo 2", sans-serif; font-weight: 600;
    font-size: 28px; color: var(--green); line-height: 1.1;
  }
  .identity-title {
    font-size: 15px; color: var(--white); margin-top: 2px;
  }
  .contact {
    position: absolute; left: 40px; bottom: 48px;
    list-style: none; color: var(--white);
    font-size: 15px; line-height: 1.45;
  }
  .contact-row { display: flex; align-items: center; gap: 8px; }
  .icon { width: 15px; height: 15px; flex: none; }
  .card-back .wordmark {
    position: absolute; right: 44px; bottom: 54px;
    display: flex; align-items: center; gap: 12px;
  }
  .card-back .wordmark-dot { width: 38px; height: 38px; background: var(--green); border-radius: 6px; }
  .card-back .wordmark-name {
    font-weight: 400; font-size: 64px; line-height: 1; color: var(--grey);
  }
</style>
</head>
<body>
  <section class="card card-front">
    <div class="wordmark">
      <span class="wordmark-dot"></span>
      <span class="wordmark-name">brovix</span>
    </div>
  </section>

  <section class="card card-back">
    <svg class="accent-arc" width="40" height="110" viewBox="0 0 40 110">
      <path d="M0 0 H30 Q10 40 0 110 Z" fill="var(--green)"/>
    </svg>
    <div class="identity">
      <p class="identity-name">Halyna Dorosh</p>
      <p class="identity-title">Director of Marketing</p>
    </div>
    <ul class="contact">
      <li class="contact-row">20517 - 87 Ave. Edmonton,</li>
      <li class="contact-row">AB, Canada T6K 4N8</li>
      <li class="contact-row">
        <svg class="icon" viewBox="0 0 16 16"><circle cx="8" cy="8" r="8" fill="var(--green)"/><path d="M5 4.5h2l.6 2-1 .8a5 5 0 0 0 2.1 2.1l.8-1 2 .6v2c0 .4-.4.8-.8.8A6.8 6.8 0 0 1 4.2 5.3c0-.4.4-.8.8-.8z" fill="var(--card)"/></svg>
        +1 780-555-0184
      </li>
      <li class="contact-row">
        <svg class="icon" viewBox="0 0 16 16"><circle cx="8" cy="8" r="8" fill="var(--green)"/><rect x="5.5" y="3.5" width="5" height="9" rx="1" fill="var(--card)"/><rect x="6.5" y="4.7" width="3" height="5.6" fill="var(--green)"/><circle cx="8" cy="11.4" r=".5" fill="var(--green)"/></svg>
        +1 780-555-0239
      </li>
      <li class="contact-row">
        <svg class="icon" viewBox="0 0 16 16"><circle cx="8" cy="8" r="8" fill="var(--green)"/><rect x="4" y="5" width="8" height="6" rx="1" fill="var(--card)"/><path d="M4.3 5.4 8 8.4l3.7-3" stroke="var(--green)" stroke-width="1" fill="none"/></svg>
        halya.dorosh@quillmail.example
      </li>
      <li class="contact-row">
        <svg class="icon" viewBox="0 0 16 16"><circle cx="8" cy="8" r="8" fill="var(--green)"/><circle cx="8" cy="8" r="4" fill="none" stroke="var(--card)" stroke-width="1.2"/><path d="M4 8h8M8 4c-1.6 2.4-1.6 5.6 0 8M8 4c1.6 2.4 1.6 5.6 0 8" stroke="var(--card)" stroke-width="1" fill="none"/></svg>
        brovix.example
      </li>
    </ul>
    <div class="wordmark">
      <span class="wordmark-dot"></span>
      <span class="wordmark-name">brovix</span>
    </div>
  </section>
</body>
</html>
```